Business card design for holistic health care clinic

We need a double-sided business card design for our holistic health care clinic that integrates our logo design and also its color scheme. My business is called Valmira. It is an integrative medicine clinic. You have already done the logo for me. Please ensure an elegant and upscale design that is not cluttered, but still has all the necessary information (please see below for details).

Target Market(s)

Wellness, fitness, rehabilitation for educated, well-traveled open-minded clients who are focused on natural, organic, balanced and preventive healthcare and lifestyle.

Industry/Entity Type

Medical

Contact Information for Business Card

Modern, clean.

Number of Pages Required

1 page

Font styles to use
Serif
Sans Serif

Colors

Designer to choose colors to be used in the design.

Requirements
Must have
• Logo on one side, all other information on the other side.
• Other information should include:
• Tobias Wrenfeld - DOE, CPT, LMT
• 4100 East Marrow Drive
• Austin, TX 78119
• 512 555 0148
• 818 555 0192
• info@ValmiraHealth.example
• t.wrenfeld@ValmiraHealth.example
Nice to have
• Darker background on front - but not totally black - shaded/dark gray.

```html
<!DOCTYPE html>
<html lang="en">
<head>
<meta charset="utf-8">
<title>Valmira – Business Card</title>
<link rel="stylesheet" href="https://fonts.googleapis.com/css2?family=Nunito:wght@700;800&family=Roboto:wght@400;500&family=Roboto+Condensed:wght@700&display=swap">
<style>
  :root {
    --backdrop: #e6ded3;
    --card-dark: #2a2a2a;
    --card-light: #f2f2f2;
    --brand-blue: #0f8fcf;
    --text-light: #f1f1f1;
    --text-grey: #555555;
    --shadow: 0 3px 6px rgba(0,0,0,0.35);
  }
  * { margin: 0; padding: 0; box-sizing: border-box; }
  html, body {
    width: 1200px; height: 960px; overflow: hidden;
    background: var(--backdrop);
  }
  .stage { position: relative; width: 1200px; height: 960px; }

  .card {
    position: absolute; width: 600px; height: 343px;
    box-shadow: var(--shadow); overflow: hidden;
  }
  .card--front { left: 314px; top: 113px; background: radial-gradient(ellipse at 55% 35%, #333 0%, var(--card-dark) 70%); }
  .card--back  { left: 311px; top: 472px; background: var(--card-light); }

  /* Front */
  .web-band {
    position: absolute; left: 0; top: 92px; width: 36px; height: 251px;
    background: var(--brand-blue);
  }
  .web-address {
    position: absolute; left: 50%; top: 50%;
    transform: translate(-50%, -50%) rotate(-90deg);
    font-family: "Roboto", sans-serif; font-size: 12.5px; letter-spacing: 1.6px;
    color: var(--text-light); white-space: nowrap;
  }
  .brand-block--front {
    position: absolute; right: 40px; top: 74px; text-align: center;
  }
  .brand-name {
    font-family: "Nunito", sans-serif; font-weight: 800; color: var(--brand-blue);
    line-height: 1; letter-spacing: 1px;
  }
  .brand-block--front .brand-name { font-size: 54px; }
  .brand-tagline {
    font-family: "Nunito", sans-serif; font-weight: 800; color: var(--brand-blue);
  }
  .brand-block--front .brand-tagline { font-size: 16px; margin-top: 2px; }

  .person-name {
    position: absolute; left: 61px; top: 212px;
    font-family: "Roboto Condensed", sans-serif; font-weight: 700; font-size: 21px;
    color: var(--brand-blue); letter-spacing: 0.3px;
  }
  .person-credentials {
    position: absolute; left: 61px; top: 235px;
    font-family: "Roboto Condensed", sans-serif; font-weight: 700; font-size: 12px;
    color: var(--brand-blue);
  }
  .rule { position: absolute; height: 1px; background: var(--brand-blue); }
  .rule--name { left: 151px; right: 40px; top: 243px; }
  .rule--bottom { left: 61px; right: 40px; top: 315px; }

  .contact {
    position: absolute; top: 260px;
    font-family: "Roboto", sans-serif; font-size: 14.5px; line-height: 19px;
    color: var(--text-light);
  }
  .contact--phones { left: 62px; }
  .contact--phones b { color: var(--brand-blue); font-weight: 500; }
  .contact--address { left: 208px; }
  .contact-divider {
    position: absolute; left: 188px; top: 265px; width: 3px; height: 31px;
    background: var(--brand-blue);
  }

  /* Back */
  .brand-block--back {
    position: absolute; left: 0; right: 0; top: 148px; text-align: center;
  }
  .brand-block--back .brand-name { font-size: 64px; }
  .brand-block--back .brand-tagline { font-size: 18px; margin-top: 0; }
  .slogan {
    position: absolute; left: 0; right: 0; top: 291px; text-align: center;
    font-family: "Roboto", sans-serif; font-size: 14.5px; color: var(--text-grey);
  }
</style>
</head>
<body>
<main class="stage">
  <section class="card card--front" aria-label="Business card front">
    <div class="web-band">
      <span class="web-address">www.ValmiraHealth.example</span>
    </div>
    <div class="brand-block brand-block--front">
      <div class="brand-name">VALMIRA</div>
      <div class="brand-tagline">Integrative Holistic Medicine</div>
    </div>

    <h1 class="person-name">TOBIAS WRENFELD</h1>
    <p class="person-credentials">DOE, CPT, LMT</p>
    <div class="rule rule--name"></div>

    <p class="contact contact--phones"><b>P:</b> 512 555 0148<br><b>C:</b> 818 555 0192</p>
    <div class="contact-divider"></div>
    <p class="contact contact--address">t.wrenfeld@ValmiraHealth.example<br>4100 East Marrow Drive, Austin, TX 78119</p>
    <div class="rule rule--bottom"></div>
  </section>

  <section class="card card--back" aria-label="Business card back">
    <div class="brand-block brand-block--back">
      <div class="brand-name">VALMIRA</div>
      <div class="brand-tagline">Integrative Holistic Medicine</div>
    </div>
    <p class="slogan">it’s all about you – your health, your objectives</p>
  </section>
</main>
</body>
</html>
```